Need a website where people can find information about the newly formed Northmere Valuation Oversight Board. Soon after, we will need a place to publish our findings as we audit each municipality in the State of Wisconsin. I have a logo (designed by Artwell Hub), a MS Word document showing the content and a set of images to choose from that we can purchase from Pixmarla.com (found here https://www.pixmarla.com/collaboration/boards/-Xq7TbLwRmNoPzYkAuH-Jd)

```html
<!DOCTYPE html>
<html lang="en">
<head>
<meta charset="utf-8">
<title>Northmere Valuation Oversight Board</title>
<link href="https://fonts.googleapis.com/css2?family=Montserrat:wght@400;500;600;700;800&family=Oswald:wght@500;600&display=swap" rel="stylesheet">
<style>
:root{
  --green:#2f7a17;
  --green-dark:#25650f;
  --green-light:#3d8c22;
  --grey-bg:#ececec;
  --ink:#1f1f1f;
  --body:#444;
  --black:#0b0b0b;
  --white:#fff;
  --footer-text:#eee;
  --footer-muted:#bbb;
}
*{box-sizing:border-box;margin:0;padding:0}
html,body{width:1200px;height:4409px;overflow:hidden}
body{font-family:"Montserrat",sans-serif;color:var(--ink);background:var(--white);position:relative}
.abs{position:absolute}
.photo{position:absolute}
.heading{font-family:"Oswald",sans-serif;font-weight:600;text-transform:uppercase;letter-spacing:.5px;line-height:1}
.sub{font-weight:500;text-transform:uppercase;color:var(--green);font-size:18px;letter-spacing:.3px}
.para{font-size:13.5px;line-height:22px;color:var(--body);text-align:justify}
.btn{position:absolute;display:flex;align-items:center;justify-content:space-between;background:var(--green);color:var(--white);font-size:11px;font-weight:600;text-transform:uppercase;padding:0 8px 0 18px;box-shadow:0 0 0 3px #d9d9d9 inset}
.btn .arrow{width:24px;height:24px;border-radius:50%;background:var(--white);display:flex;align-items:center;justify-content:center}
.name-mark{display:flex;flex-direction:column;align-items:center;justify-content:center;background:var(--green);color:var(--white);font-weight:700}

/* header */
.topbar{left:425px;top:0;width:775px;height:33px;background:var(--green);display:flex;justify-content:space-around;align-items:center;font-size:11.5px;color:var(--white);font-weight:500;z-index:2}
.hero{left:0;top:0;width:1200px;height:668px;background:linear-gradient(180deg,#55585a 0%,#6b6e6d 22%,#4f6a3a 40%,#3f7a2a 55%,#8a5a2e 68%,#a86b30 82%,#6d4420 100%)}
.brand{left:111px;top:5px;width:91px;height:101px;font-size:16px;z-index:2}
.contact-row{left:500px;top:45px;display:flex;align-items:center;gap:40px;color:var(--white);font-size:12px;font-weight:500}
.contact-row span{display:flex;align-items:center;gap:10px}
.social{display:flex;gap:10px}
.social i{width:30px;height:30px;border:1.5px solid var(--white);border-radius:50%;display:block}
.rule{left:210px;top:80px;width:880px;height:1px;background:rgba(255,255,255,.4)}
.nav{left:220px;top:96px;display:flex;gap:40px;font-size:12.5px;color:#e8e8e8}
.nav .active{color:var(--white);font-weight:600;border-bottom:2px solid var(--white);padding-bottom:6px}
.hero-title{left:111px;top:255px;font-size:56px;font-weight:800;color:var(--white);letter-spacing:1px;line-height:1}
.hero-text{left:111px;top:318px;font-size:17px;line-height:24px;font-weight:500;color:var(--white)}
.hero-btn{left:111px;top:385px;width:214px;height:45px;font-size:15px;box-shadow:none}
.hero-btn .arrow{width:30px;height:30px}
.slide-arrow{width:60px;height:60px;border:2px solid var(--white);border-radius:50%;display:flex;align-items:center;justify-content:center}
.dots{left:566px;top:622px;display:flex;gap:8px}
.dots i{width:10px;height:10px;border-radius:50%;border:1.5px solid var(--white);display:block}
.dots i.on{background:var(--white)}

/* who */
.who{left:0;top:668px;width:1200px;height:505px;background:var(--grey-bg)}

/* uniform */
.uniform{left:0;top:1649px;width:1200px;height:494px;background:var(--green)}
.center{left:0;width:1200px;text-align:center;color:var(--white)}

/* blog */
.blog{left:0;top:2796px;width:1200px;height:760px;background:radial-gradient(circle at 30% 40%,#3e8a23,#2f7a17 60%,#276a12)}
.card{position:absolute;top:2984px;width:308px;height:423px;background:var(--white);box-shadow:0 2px 6px rgba(0,0,0,.25)}
.card .img{height:204px}
.card .meta{margin:14px 14px 0;font-size:12px;font-weight:600;color:var(--green)}
.card h3{margin:6px 14px 0;font-size:16px;font-weight:500;color:var(--ink);white-space:nowrap}
.card p{margin:8px 14px 0;font-size:11.5px;line-height:20.5px;color:var(--body);font-weight:500}
.card .down{position:absolute;left:145px;bottom:10px}
.outline-btn{left:526px;top:3436px;width:147px;height:34px;border:1.5px solid var(--white);color:var(--white);font-size:11px;font-weight:600;display:flex;align-items:center;justify-content:space-between;padding:0 8px 0 18px}
.outline-btn .arrow{width:24px;height:24px;border-radius:50%;background:var(--white);display:flex;align-items:center;justify-content:center}

/* contact */
.label{font-size:11px;font-weight:500;color:var(--ink)}
.field{position:absolute;border:1px solid #cfcfcf;font-size:10px;color:#777;padding:10px}

/* footer */
.footer{left:0;top:4049px;width:1200px;height:360px;background:var(--black)}
.fhead{position:absolute;top:4105px;font-size:19px;font-weight:700;color:var(--white)}
.flist{position:absolute;top:4164px;font-size:12.5px;line-height:26px;color:var(--footer-text)}
.fcontact{position:absolute;font-size:12.5px;line-height:17px;color:var(--white)}
.flabel{font-size:10px;color:var(--footer-muted)}
.fbottom{position:absolute;color:var(--white)}
</style>
</head>
<body>

<!-- Hero -->
<div class="hero abs" role="img" aria-label="Farm scene with red barn and silos beside a golden cornfield under a cloudy sky"></div>
<div class="topbar abs"><span>Audits</span><span>NVOB Recommendations</span><span>Meet the Volunteers</span><span>Corrections</span><span>Blog</span><span>Donate</span></div>
<div class="brand abs name-mark">NVOB</div>
<div class="contact-row abs">
  <span><svg width="14" height="14" viewBox="0 0 24 24"><path fill="#fff" d="M6.6 10.8a15 15 0 006.6 6.6l2.2-2.2c.3-.3.7-.4 1-.2 1.1.4 2.3.6 3.6.6.6 0 1 .4 1 1V20c0 .6-.4 1-1 1A17 17 0 013 4c0-.6.4-1 1-1h3.5c.6 0 1 .4 1 1 0 1.3.2 2.5.6 3.6.1.3 0 .7-.2 1z"/></svg>+1 (457) 555 0142</span>
  <span><svg width="16" height="12" viewBox="0 0 16 12"><rect x=".5" y=".5" width="15" height="11" fill="none" stroke="#fff"/><path d="M.5.5L8 7 15.5.5" fill="none" stroke="#fff"/></svg>nvob.info@mail.com</span>
  <span class="social"><i></i><i></i><i></i></span>
</div>
<div class="rule abs"></div>
<nav class="nav abs"><span class="active">Home</span><span>Who We Are</span><span>Wisconsin's Non-Uniform Property Tax Problem</span><span>What is Uniform Taxation?</span><span>Blog</span><span>Contact Us</span></nav>
<div class="hero-title abs">NVOB</div>
<div class="hero-text abs">Kaerspiciatis unde omnis istenatus errorsit<br>voluptatem accusantium doloremque</div>
<div class="btn hero-btn">Get Started<span class="arrow"><svg width="14" height="12" viewBox="0 0 14 12"><path d="M1 6h11M7 1l5 5-5 5" stroke="#2f7a17" stroke-width="2" fill="none"/></svg></span></div>
<div class="slide-arrow abs" style="left:23px;top:304px"><svg width="20" height="14" viewBox="0 0 20 14"><path d="M19 7H2M8 1L2 7l6 6" stroke="#fff" stroke-width="2" fill="none"/></svg></div>
<div class="slide-arrow abs" style="left:1117px;top:304px"><svg width="20" height="14" viewBox="0 0 20 14"><path d="M1 7h17M12 1l6 6-6 6" stroke="#fff" stroke-width="2" fill="none"/></svg></div>
<div class="dots abs"><i></i><i class="on"></i><i></i><i></i></div>

<!-- Who we are -->
<section class="who abs"></section>
<div class="photo" style="left:8px;top:707px;width:282px;height:431px;background:var(--green)" role="img" aria-label="State outline map in green"></div>
<div class="photo" style="left:75px;top:734px;width:524px;height:348px;background:linear-gradient(180deg,#2c63c9 0%,#5a8fe0 45%,#d8d8d0 60%,#3f6b2a 85%,#2e4f22 100%)" role="img" aria-label="State capitol building with white dome under blue sky"></div>
<h2 class="heading abs" style="left:639px;top:733px;font-size:42px">Who We Are</h2>
<div class="sub abs" style="left:637px;top:787px">Ksoknrspiciatis unde omniside natuserro</div>
<p class="para abs" style="left:639px;top:824px;width:443px">Perspiciatis unde omnis iksoekste natus error sit voluptatem accusantium doloremque laudokseantium, toseiuaootam rems aperiam, eaque ipsa quae ab illo inventore veritatis et quasi architecto beatae vitae dicta kseiosunt explicabseis iko. Nemo eniseghhm ipsam voluptatem quia voluptas sit aspernatur aut odit autfugit sedoquia consequuntur klseokjlseoosei losimagni dolores eos qui ratione voluptatem sequi nesciunt.</p>
<div class="btn" style="left:640px;top:1013px;width:146px;height:35px">Learn More<span class="arrow"><svg width="12" height="10" viewBox="0 0 14 12"><path d="M1 6h11M7 1l5 5-5 5" stroke="#2f7a17" stroke-width="2" fill="none"/></svg></span></div>

<!-- Recommendations -->
<div class="photo" style="left:640px;top:1173px;width:560px;height:476px;background:linear-gradient(100deg,#ffffff 0%,#ffffff 20%,#c9d0d6 40%,#6f7f8f 70%,#9aa6b0 100%)" role="img" aria-label="Man reviewing a document while working at a laptop"></div>
<h2 class="heading abs" style="left:111px;top:1256px;font-size:42px">NVOB Recommendations</h2>
<div class="sub abs" style="left:109px;top:1310px">Ksoknrspiciatis unde omniside natuserro</div>
<p class="para abs" style="left:111px;top:1342px;width:514px">Perspiciatis unde omnis iksoekste natus error sit voluptatem accusantium doloremque laudantium, totam rems aperiam, eaque ipsa quae ab illo inventore veritatis et quasi architecto beatae vitae dicta sunt explicabo. Nemo eniseghhm ipsam voluptatem quia voluptas sit aspernatur aut odit aut fugit, sed quia consequuntur klseoimagni dolores eos qui ratione voluptatem sequi nesciunt.&nbsp; quia voluptas sit aspernatur aut odit aut fugit, sed quia csequi nesciunt.</p>
<div class="btn" style="left:111px;top:1530px;width:148px;height:33px">Learn More<span class="arrow"><svg width="12" height="10" viewBox="0 0 14 12"><path d="M1 6h11M7 1l5 5-5 5" stroke="#2f7a17" stroke-width="2" fill="none"/></svg></span></div>

<!-- Uniform taxation -->
<section class="uniform abs"></section>
<h2 class="heading abs center" style="top:1733px;font-size:42px">What is Uniform Taxation?</h2>
<div class="abs center" style="top:1782px;font-size:18px;font-weight:500">KSOKNRSPICIATIS UNDE OMNISISTE NATUSERRO</div>
<p class="abs center" style="left:157px;width:886px;top:1816px;font-size:13.5px;line-height:22px">Perspiciatis unde omnis iksoekste natus error sit voluptatem accusantium doloremque laudantium, totam rems aperiam, eaque ipsa quae ab illo inventore veritatis et quasi architecto beatae vitae dicta sunt explicabo. Nemo eniseghhm ipsam voluptatem quia voluptas sit aspernatur aut odit aut fugit, sed quia consequuntur klseoimagni dolores eos qui ratione.</p>
<div class="photo" style="left:240px;top:1929px;width:720px;height:384px;background:linear-gradient(180deg,#3a6fc0 0%,#8fb2e0 35%,#b9a37a 52%,#4a6a7e 62%,#2f5e86 100%)" role="img" aria-label="City skyline reflected in calm lakeside water"></div>

<!-- Corrections -->
<div class="abs name-mark" style="left:205px;top:2368px;width:300px;height:320px;font-size:44px">NVOB</div>
<h2 class="heading abs" style="left:613px;top:2394px;font-size:42px">Corrections</h2>
<div class="sub abs" style="left:613px;top:2448px">Ksoknrspiciatis unde omniside natuserro</div>
<p class="para abs" style="left:616px;top:2484px;width:420px">Perspiciatis unde omnis iksoekste natus error sit voluptatem accusantium doloremque laudantium, totam rems aperiam, eaque ipsa quae ab illo inventore veritatis et quasi architecto beatae vitae dicta sunt explicabo. Nemo eniseghhm ipsam voluptatem quia voluptas sit aspernatur aut odit aut fugit, sed quia consequuntur klseoimagni dolores eos qui ratione voluptatem sequi nesciunt.</p>
<div class="btn" style="left:616px;top:2676px;width:148px;height:33px">Learn More<span class="arrow"><svg width="12" height="10" viewBox="0 0 14 12"><path d="M1 6h11M7 1l5 5-5 5" stroke="#2f7a17" stroke-width="2" fill="none"/></svg></span></div>

<!-- Blog -->
<section class="blog abs" role="img" aria-label="Faint aerial view of green farmland"></section>
<h2 class="heading abs center" style="top:2877px;font-size:42px">Blog</h2>
<div class="abs center" style="top:2933px;font-size:18px;font-weight:500">KSOKNRSPICIATIS UNDE OMNISISTE NATUSERRO</div>

<article class="card" style="left:111px"><div class="img" style="background:linear-gradient(135deg,#3c3c3c,#9a9a9a,#4a4a4a)" role="img" aria-label="Metal gears engraved with audit and review words"></div><div class="meta">Dec 20, 2021 I 2 Comments</div><h3>Oskamnis iste natus error sitvolup</h3><p>Ksomnis iste natus error sit voluptatem accusantium doloremque laudantium, totam rem aperiam, eaque ipsa quae ab illo inventore veritatis et quasi architecto beatae vitae dicta sunt explicabo. Nemo enim ipsam</p><svg class="down" width="16" height="18" viewBox="0 0 16 18"><path d="M8 1v15M2 10l6 6 6-6" stroke="#2f7a17" stroke-width="2" fill="none"/></svg></article>
<article class="card" style="left:445px"><div class="img" style="background:linear-gradient(135deg,#2a2a2a,#bfbfbf 55%,#f0f0f0)" role="img" aria-label="Hand with pen over printed figures beside a keyboard"></div><div class="meta">Dec 20, 2021 I 2 Comments</div><h3>Oskamnis iste natus error sitvolup</h3><p>Ksomnis iste natus error sit voluptatem accusantium doloremque laudantium, totam rem aperiam, eaque ipsa quae ab illo inventore veritatis et quasi architecto beatae vitae dicta sunt explicabo. Nemo enim ipsam</p><svg class="down" width="16" height="18" viewBox="0 0 16 18"><path d="M8 1v15M2 10l6 6 6-6" stroke="#2f7a17" stroke-width="2" fill="none"/></svg></article>
<article class="card" style="left:779px"><div class="img" style="background:linear-gradient(180deg,#d9c8a0,#c0763a 55%,#8a5a2a)" role="img" aria-label="Lone tree in a field beside a property tax note"></div><div class="meta">Dec 20, 2021 I 2 Comments</div><h3>Oskamnis iste natus error sitvolup</h3><p>Ksomnis iste natus error sit voluptatem accusantium doloremque laudantium, totam rem aperiam, eaque ipsa quae ab illo inventore veritatis et quasi architecto beatae vitae dicta sunt explicabo. Nemo enim ipsam</p><svg class="down" width="16" height="18" viewBox="0 0 16 18"><path d="M8 1v15M2 10l6 6 6-6" stroke="#2f7a17" stroke-width="2" fill="none"/></svg></article>
<div class="outline-btn abs">VIEW MORE<span class="arrow"><svg width="12" height="10" viewBox="0 0 14 12"><path d="M1 6h11M7 1l5 5-5 5" stroke="#2f7a17" stroke-width="2" fill="none"/></svg></span></div>

<!-- Contact -->
<div class="abs name-mark" style="left:111px;top:3612px;width:117px;height:125px;font-size:20px">NVOB</div>
<h2 class="abs" style="left:111px;top:3770px;font-size:32px;font-weight:700;line-height:44px">Get In Touch With<br>Us NVOB</h2>
<div class="abs" style="left:111px;top:3864px;font-size:19px;line-height:34px;font-weight:500">Reach out to discuss your needs.<br>nvob.info@mail.com</div>

<div class="abs label" style="left:497px;top:3642px">YOUR NAME</div>
<div class="abs label" style="left:782px;top:3642px">LAST NAME</div>
<div class="field" style="left:497px;top:3659px;width:255px;height:37px">Ksoeins</div>
<div class="field" style="left:782px;top:3659px;width:255px;height:37px">Smlseij</div>
<div class="abs label" style="left:497px;top:3720px">EMAIL ADDRESS</div>
<div class="abs label" style="left:782px;top:3720px">PHONE</div>
<div class="field" style="left:497px;top:3739px;width:255px;height:38px">ksoeins.smlseij@example.com</div>
<div class="field" style="left:782px;top:3739px;width:255px;height:38px">608 555 0199</div>
<div class="abs label" style="left:497px;top:3799px">MESSAGE</div>
<div class="field" style="left:497px;top:3816px;width:541px;height:98px">Hi, do you have a momment to talk abo...</div>
<div class="btn" style="left:498px;top:3927px;width:146px;height:33px;box-shadow:none">Submit<span class="arrow"><svg width="12" height="10" viewBox="0 0 14 12"><path d="M1 6h11M7 1l5 5-5 5" stroke="#2f7a17" stroke-width="2" fill="none"/></svg></span></div>

<!-- Footer -->
<footer class="footer abs"></footer>
<h4 class="fhead" style="left:110px">Quick Links</h4>
<h4 class="fhead" style="left:666px">Support</h4>
<h4 class="fhead" style="left:786px">Links</h4>
<h4 class="fhead" style="left:912px">Contact Us</h4>
<div class="flist" style="left:111px">Home<br>Who We Are<br>Wisconsin's Non-Uniform Property Tax Problem<br>What is Uniform Taxation?<br>Blog<br>Contact Us</div>
<div class="flist" style="left:452px">Audits<br>NVOB Recommendations<br>Meet the Volunteers<br>Corrections<br>Blog<br>Donate</div>
<div class="flist" style="left:667px">Team<br>About Us<br>Careers<br>Our Values</div>
<div class="flist" style="left:788px">Copyright<br>Legal<br>Privacy<br>Accessibility<br>Sitemap</div>
<svg class="abs" style="left:910px;top:4176px" width="16" height="22" viewBox="0 0 16 22"><path d="M8 1a7 7 0 00-7 7c0 5 7 13 7 13s7-8 7-13a7 7 0 00-7-7z" fill="#3d9a24"/><circle cx="8" cy="8" r="2.5" fill="#0b0b0b"/></svg>
<svg class="abs" style="left:910px;top:4248px" width="16" height="16" viewBox="0 0 24 24"><path fill="#3d9a24" d="M6.6 10.8a15 15 0 006.6 6.6l2.2-2.2c.3-.3.7-.4 1-.2 1.1.4 2.3.6 3.6.6.6 0 1 .4 1 1V20c0 .6-.4 1-1 1A17 17 0 013 4c0-.6.4-1 1-1h3.5c.6 0 1 .4 1 1 0 1.3.2 2.5.6 3.6.1.3 0 .7-.2 1z"/></svg>
<svg class="abs" style="left:910px;top:4298px" width="16" height="12" viewBox="0 0 16 12"><rect x=".5" y=".5" width="15" height="11" fill="none" stroke="#3d9a24"/><path d="M.5.5L8 7 15.5.5" fill="none" stroke="#3d9a24"/></svg>
<div class="fcontact" style="left:937px;top:4166px"><span class="flabel">Address</span><br>1234 Harrow Lane, Fenwick<br>Texas, USA</div>
<div class="fcontact" style="left:937px;top:4236px"><span class="flabel">Phone</span><br>+1 (457) 555 0142</div>
<div class="fcontact" style="left:937px;top:4284px"><span class="flabel">Mail</span><br>nvob.info@mail.com</div>
<div class="abs" style="left:1122px;top:4308px;width:44px;height:44px;border-radius:50%;background:var(--green);display:flex;align-items:center;justify-content:center"><svg width="14" height="10" viewBox="0 0 14 10"><path d="M1 8l6-6 6 6" stroke="#fff" stroke-width="2" fill="none"/></svg></div>
<div class="abs" style="left:111px;top:4333px;width:978px;height:1px;background:#333"></div>
<div class="fbottom" style="left:111px;top:4361px;font-size:12.5px">Copyright © 2022 | All Rights Reserved</div>
<div class="fbottom" style="left:846px;top:4362px;font-size:11px;display:flex;gap:22px">Terms &amp; Conditions<span style="color:#666">|</span>Privacy Policy</div>

</body>
</html>
```